A design led business card for the construction industry

High-end business card to match logo. White logo on dark grey/off black to the front. Matching dark font on white to back, possibly with logo design again.

We offer construction and project management services to commercial and private clients in the UK. Projetcs range from newbuilds, conversion of listed buildings and refurbishments and extensions of existing homes. Our focus is on quality and attention to detail using the highest skills.

Contact Information for Business Card

Name; Dorian Keble BSc
Position; Project Manager
Mobile; 07962 408 175
Tel; 01632 960457
email; dorian@stonevale.co.uk
web; www.stonevale.co.uk
Address; Aldmere on Wey, KX4 7PW

Colors

Designer to choose only greyscale colors for use in the design.

Requirements
Must have
• To include the below description of the business,

CONSTRUCTION - PROJECT MANAGEMENT
Nice to have
• The posibility of the top back of the card being used as a ruler. So will have a measurement to scale in mm or an architect scale of 1:50
Should not have
• Should not be portrait

```html
<!DOCTYPE html>
<html lang="en">
<head>
<meta charset="utf-8">
<title>Stonevale – Business Card</title>
<link href="https://fonts.googleapis.com/css2?family=Arimo:wght@400;700&display=swap" rel="stylesheet">
<style>
  :root {
    --stage: #000000;
    --card: #2e2e30;
    --card-edge: #3a3a3c;
    --ink: #ffffff;
    --ink-soft: #e6e6e6;
    --ink-muted: #9a9a9c;
    --rule: #5a5a5c;
  }
  html, body {
    margin: 0;
    padding: 0;
    width: 1200px;
    height: 900px;
    overflow: hidden;
    background: var(--stage);
    font-family: "Arimo", Arial, sans-serif;
  }
  .stage {
    position: relative;
    width: 1200px;
    height: 900px;
  }
  .card {
    position: absolute;
    width: 458px;
    height: 281px;
    background: var(--card);
    border-radius: 14px;
    box-shadow: inset 0 0 0 1px var(--card-edge);
    color: var(--ink);
  }
  .card--contact { left: 138px; top: 265px; }
  .card--brand { left: 625px; top: 268px; }

  .wordmark {
    position: absolute;
    margin: 0;
    font-weight: 400;
    color: var(--ink);
    letter-spacing: 0.42em;
    white-space: nowrap;
  }
  .card--contact .brand-block {
    position: absolute;
    left: 26px;
    width: 190px;
    top: 100px;
    display: flex;
    flex-direction: column;
    align-items: center;
    gap: 14px;
  }
  .brand-square {
    width: 30px;
    height: 30px;
    border: 2px solid var(--ink);
    box-sizing: border-box;
  }
  .card--contact .wordmark {
    position: static;
    font-size: 16px;
    margin-right: -0.42em;
  }

  .divider {
    position: absolute;
    left: 230px;
    top: 75px;
    width: 1px;
    height: 132px;
    background: var(--rule);
  }

  .details {
    position: absolute;
    left: 248px;
    top: 71px;
    font-size: 13.5px;
    line-height: 1.2;
    color: var(--ink-soft);
  }
  .person-name {
    margin: 0;
    font-size: 15.5px;
    font-weight: 700;
    color: var(--ink);
  }
  .person-name .credential { font-weight: 400; }
  .person-role { margin: 0 0 13px; }
  .contact-list {
    list-style: none;
    margin: 0 0 12px;
    padding: 0;
  }
  .contact-list li {
    display: flex;
    align-items: center;
    gap: 5px;
    height: 16.5px;
  }
  .contact-list svg {
    width: 11px;
    height: 11px;
    flex: none;
    fill: none;
    stroke: var(--ink);
    stroke-width: 1.5;
  }
  .address { margin: 0; }

  .card--brand .brand-block {
    position: absolute;
    left: 0;
    right: 0;
    top: 112px;
    display: flex;
    flex-direction: column;
    align-items: center;
  }
  .card--brand .brand-square {
    width: 40px;
    height: 40px;
    margin-bottom: 18px;
  }
  .card--brand .wordmark {
    position: static;
    font-size: 21px;
    margin-right: -0.42em;
  }
  .tagline {
    margin: 18px 0 0;
    font-size: 11px;
    color: var(--ink-muted);
    letter-spacing: 0.01em;
  }
</style>
</head>
<body>
<main class="stage">

  <section class="card card--contact" aria-label="Business card front">
    <div class="brand-block">
      <div class="brand-square"></div>
      <p class="wordmark">STONEVALE</p>
    </div>

    <div class="divider"></div>

    <div class="details">
      <p class="person-name">DORIAN KEBLE <span class="credential">BSc</span></p>
      <p class="person-role">Project Manager</p>
      <ul class="contact-list">
        <li>
          <svg viewBox="0 0 12 12" aria-hidden="true"><rect x="3" y="0.8" width="6" height="10.4" rx="1"/><line x1="5" y1="9.4" x2="7" y2="9.4"/></svg>
          07962 408 175
        </li>
        <li>
          <svg viewBox="0 0 12 12" aria-hidden="true"><path d="M2.2 1.2 L4.2 1.2 L5 3.6 L3.8 4.6 C4.5 6.2 5.8 7.5 7.4 8.2 L8.4 7 L10.8 7.8 L10.8 9.8 C10.8 10.4 10.3 10.8 9.8 10.8 C5.2 10.5 1.5 6.8 1.2 2.2 C1.2 1.7 1.6 1.2 2.2 1.2 Z"/></svg>
          01632 960457
        </li>
        <li>
          <svg viewBox="0 0 12 12" aria-hidden="true"><rect x="0.8" y="2.2" width="10.4" height="7.6"/><polyline points="0.8,2.2 6,6.6 11.2,2.2"/></svg>
          dorian@stonevale.co.uk
        </li>
        <li>
          <svg viewBox="0 0 12 12" aria-hidden="true"><circle cx="6" cy="6" r="5.2"/><ellipse cx="6" cy="6" rx="2.3" ry="5.2"/><line x1="0.8" y1="6" x2="11.2" y2="6"/><line x1="1.6" y1="3.4" x2="10.4" y2="3.4"/><line x1="1.6" y1="8.6" x2="10.4" y2="8.6"/></svg>
          www.stonevale.co.uk
        </li>
      </ul>
      <p class="address">Aldmere on Wey, KX4 7PW</p>
    </div>
  </section>

  <section class="card card--brand" aria-label="Business card back">
    <div class="brand-block">
      <div class="brand-square"></div>
      <p class="wordmark">STONEVALE</p>
      <p class="tagline">CONSTRUCTION - PROJECT MANAGEMENT</p>
    </div>
  </section>

</main>
</body>
</html>
```